Real Estate Webpage Design

We have an existing website: ferndaleestatecollective.com.au
We focus customised service mainly on Property Management and second-hand property sales.
We are not entirely happy about the current design and layout can stay roughly the same as the back end coding is linked to a CRM system.
We would like to see the design are more reachable to our clients and appearing.
Please check our Website Design Draft for more details.

Industry/Entity Type

Real estate Agency

Number of Pages Required

5+ page

Font styles to use
Sans Serif

Colors

Designer to choose colors to be used in the design.

```html
<!DOCTYPE html>
<html lang="en">
<head>
<meta charset="utf-8">
<title>Ferndale Estate Collective</title>
<link href="https://fonts.googleapis.com/css2?family=Poppins:wght@400;500;600;700&display=swap" rel="stylesheet">
<style>
:root{
  --gold:#e2b33f;
  --gold-dark:#c99a28;
  --navy:#1d2939;
  --navy-mid:#2b3749;
  --footer:#1b2431;
  --ink:#1f2328;
  --muted:#5c6068;
  --line:#e4e4e4;
  --white:#ffffff;
  --panel:#f1f1f1;
}
*{box-sizing:border-box;margin:0;padding:0}
html,body{width:1200px;height:4669px;overflow:hidden}
body{font-family:'Poppins',sans-serif;color:var(--ink);background:var(--white);position:relative}
section,header,footer{position:absolute;left:0;width:1200px}
.abs{position:absolute}
.btn{position:absolute;display:flex;align-items:center;justify-content:center;background:var(--navy);color:var(--white);border-radius:30px;font-weight:500;font-size:14px}
.mark{display:inline-block;width:22px;height:22px;border:3px solid var(--gold)}
.section-title{position:absolute;left:0;width:1200px;text-align:center;font-weight:700;font-size:28px;letter-spacing:.3px}
.section-title .mark{position:absolute;left:589px;top:44px}

/* header */
.site-header{top:0;height:74px;background:var(--gold)}
.brand-box{position:absolute;left:0;top:0;width:285px;height:74px;background:var(--white);display:flex;align-items:center;padding-left:101px;gap:8px}
.brand-box .sq{width:30px;height:30px;background:var(--gold)}
.brand-box .name{font-size:25px;font-weight:600;color:var(--gold);line-height:1}
.brand-box .sub{font-size:7px;color:var(--gold);display:block;margin-top:2px}
.nav a{position:absolute;top:26px;color:var(--white);font-size:14px;text-decoration:none}
.nav a.active{font-weight:600}
.nav .under{position:absolute;left:325px;top:48px;width:11px;height:11px;border:2px solid var(--white)}
.contact-btn{left:979px;top:22px;width:116px;height:32px;font-size:14px}

/* hero */
.hero{top:74px;height:644px;background:linear-gradient(180deg,#0e1a2c 0%,#1b2a40 35%,#3b3b3a 70%,#7a6642 100%)}
.hero h1{position:absolute;left:0;width:1200px;top:240px;text-align:center;color:var(--white);font-size:40px;font-weight:700}
.hero p{position:absolute;left:200px;width:800px;top:302px;text-align:center;color:var(--white);font-size:13px;line-height:25px}
.hero .btn{left:526px;top:365px;width:143px;height:34px;font-size:13px;font-weight:600}

/* search */
.search-panel{position:absolute;left:111px;top:638px;width:977px;height:210px;background:var(--white);border-top:6px solid var(--gold);box-shadow:0 4px 18px rgba(0,0,0,.12)}
.tab{position:absolute;top:0;height:72px;width:488px;display:flex;align-items:center;padding-left:30px;gap:14px}
.tab.buy{left:0;background:var(--panel)}
.tab.sell{left:488px}
.tab .ico{width:52px;height:52px;border-radius:50%;background:var(--navy);display:flex;align-items:center;justify-content:center}
.tab h3{font-size:16px;font-weight:600;color:var(--gold)}
.tab small{font-size:11px;color:var(--ink)}
.tab .chev{position:absolute;right:30px;top:24px;width:26px;height:26px;border-radius:50%;background:var(--navy);display:flex;align-items:center;justify-content:center}
.filter{position:absolute;top:105px;height:49px;width:157px;border:1px solid var(--gold);border-radius:3px;display:flex;align-items:center;padding:0 12px;gap:6px;color:var(--gold);font-size:13px;font-weight:600}
.filter .dd{margin-left:auto}
.search-btn{position:absolute;left:788px;top:105px;width:155px;height:49px;background:var(--navy);color:var(--white);font-weight:600;font-size:15px;display:flex;align-items:center;justify-content:center;border-radius:3px;box-shadow:0 3px 8px rgba(0,0,0,.3)}

/* about */
.about{top:718px;height:714px}
.photo{position:absolute}
.about .p1{left:111px;top:216px;width:446px;height:201px;background:linear-gradient(135deg,#3a2e27,#8a6a4e 50%,#2a2624)}
.about .p2{left:111px;top:439px;width:208px;height:188px;background:linear-gradient(180deg,#6f9ed7,#c9c0ae 60%,#8f8a7f)}
.about .logo-box{position:absolute;left:341px;top:439px;width:216px;height:188px;background:var(--white);box-shadow:0 2px 12px rgba(0,0,0,.12);display:flex;align-items:center;justify-content:center;gap:10px}
.about .logo-box .sq{width:26px;height:26px;background:var(--gold)}
.about .logo-box span{font-size:28px;font-weight:600;color:var(--gold)}
.about h2{position:absolute;left:602px;top:230px;font-size:29px;font-weight:700;color:var(--gold)}
.about h4{position:absolute;left:602px;top:275px;width:490px;font-size:19px;font-weight:700;line-height:30px}
.about p{position:absolute;left:602px;top:372px;width:486px;font-size:13.4px;line-height:24px;text-align:justify;color:var(--ink)}
.about .contact{position:absolute;top:530px;font-size:14px;display:flex;align-items:center;gap:10px}
.about .btn{left:602px;top:569px;width:129px;height:42px}

/* this month */
.month{top:1432px;height:1017px;background:linear-gradient(180deg,#e0b244,#e6b947 50%,#ddb040)}
.month .section-title{top:102px;color:var(--white)}
.month .section-title b{color:var(--navy)}
.month .section-title .mark{border-color:var(--white);top:52px}
.cat{position:absolute;top:225px;width:144px;text-align:center}
.cat .circ{width:144px;height:144px;border-radius:50%;border:3px solid var(--white)}
.cat span{display:block;margin-top:22px;font-size:17px;font-weight:600;color:var(--navy)}
.cat.active span{color:var(--white)}
.card{position:absolute;top:446px;width:317px;height:461px;background:var(--white);border:5px solid var(--white);box-shadow:0 3px 12px rgba(0,0,0,.15)}
.card .img{height:232px}
.badge{position:absolute;left:12px;top:12px;padding:2px 10px;border-radius:10px;font-size:11px;color:var(--white);background:var(--gold)}
.badge.red{background:#d9261c}
.card h3{position:absolute;left:10px;top:248px;font-size:19px;font-weight:500}
.card .price{position:absolute;left:10px;top:278px;font-size:14px;color:var(--gold);font-weight:500}
.card .eye{position:absolute;right:18px;top:282px}
.card hr{position:absolute;left:10px;right:10px;top:306px;border:0;border-top:1px solid var(--line)}
.feat{position:absolute;top:325px;left:22px;display:flex;gap:42px;font-size:15px;font-weight:600}
.feat div{display:flex;align-items:center;gap:7px}
.card .addr{position:absolute;left:22px;top:365px;font-size:15px;display:flex;gap:12px;align-items:center}
.card .btn{left:22px;top:401px;width:128px;height:40px;font-size:14px}

/* team */
.team{top:2449px;height:633px}
.team .section-title{top:88px;color:var(--navy)}
.team .section-title em{font-style:normal;color:var(--gold)}
.member{position:absolute;top:183px;width:226px;height:285px}
.member .strip{position:absolute;left:0;top:0;width:49px;height:285px;background:var(--gold);display:flex;align-items:center;justify-content:center}
.member .strip span{writing-mode:vertical-rl;font-weight:700;font-size:19px;color:var(--navy);letter-spacing:.5px}
.member .photo{left:49px;top:0;width:177px;height:285px;background:linear-gradient(180deg,#565a5e,#2c2f33 60%,#1a1c1f)}
.team .btn{left:535px;top:507px;width:130px;height:42px}

/* testimonials */
.testi{top:3082px;height:531px;background:linear-gradient(180deg,#2b3748,#1f2a3a)}
.testi .section-title{top:92px;color:var(--white)}
.testi .section-title .mark{border-color:var(--white)}
.quote{position:absolute;top:196px;width:473px;height:216px;background:var(--white);text-align:center}
.quote .q1{position:absolute;left:34px;top:16px;font-size:30px;color:var(--gold);font-weight:700}
.quote .q2{position:absolute;right:88px;top:130px;font-size:30px;color:var(--gold);font-weight:700}
.quote p{position:absolute;left:64px;width:370px;top:38px;font-size:13px;line-height:23.5px}
.quote h5{position:absolute;left:0;width:473px;top:144px;font-size:14px;font-weight:700}
.quote small{position:absolute;left:0;width:473px;top:170px;font-size:13px}

/* blog */
.blog{top:3613px;height:696px}
.blog .section-title{top:84px;color:var(--navy)}
.blog .section-title em{font-style:normal;color:var(--gold)}
.post{position:absolute;top:178px;width:308px;height:446px;background:var(--panel)}
.post .photo{left:5px;top:5px;width:298px;height:227px}
.post .date{position:absolute;left:104px;top:252px;width:100px;height:22px;background:var(--gold);color:var(--white);font-size:10px;font-weight:600;display:flex;align-items:center;justify-content:center}
.post h3{position:absolute;left:0;width:308px;top:290px;text-align:center;font-size:18px;font-weight:600;line-height:27px}
.post p{position:absolute;left:16px;width:276px;top:352px;text-align:center;font-size:12.5px;line-height:23px;color:var(--muted)}

/* footer */
.site-footer{top:4309px;height:360px;background:var(--footer);color:var(--white)}
.foot-brand{position:absolute;left:111px;top:112px;display:flex;align-items:center;gap:14px}
.foot-brand .sq{width:58px;height:58px;border:4px solid var(--white)}
.foot-brand b{font-size:50px;font-weight:600;line-height:1;display:block}
.foot-brand small{font-size:14px;color:var(--gold);font-weight:600;display:block;margin-top:2px}
.socials{position:absolute;left:111px;top:208px;display:flex;gap:14px}
.socials i{width:30px;height:30px;border:2px solid var(--white);border-radius:50%;display:block}
.fcol{position:absolute;top:85px;font-size:14px}
.fcol h6{font-size:15px;font-weight:600;margin-bottom:14px}
.fcol li{list-style:none;line-height:32px}
.fcol li:before{content:"» "}
.fcol.contact li:before{content:none}
.fcol.contact li{display:flex;gap:10px;line-height:24px;margin-bottom:10px;font-size:13px}
.copyright{position:absolute;left:450px;top:300px;font-size:12px}
</style>
</head>
<body>

<header class="site-header">
  <div class="brand-box"><i class="sq"></i><div><span class="name">Ferndale</span><span class="sub">Estate Collective</span></div></div>
  <nav class="nav">
    <a class="active" style="left:312px">Home</a>
    <i class="under"></i>
    <a style="left:393px">About Us</a>
    <a style="left:498px">Leasing</a>
    <a style="left:592px">Buy</a>
    <a style="left:655px">Sell</a>
    <a style="left:718px">Our Team</a>
    <a style="left:826px">Blog</a>
    <a style="left:889px;display:flex;gap:5px;align-items:center;font-weight:600">
      <svg width="16" height="16" viewBox="0 0 16 16" fill="none" stroke="#fff" stroke-width="1.3"><circle cx="8" cy="8" r="6.5"/><ellipse cx="8" cy="8" rx="3" ry="6.5"/><path d="M1.5 8h13"/></svg>⌄ EN</a>
  </nav>
  <div class="btn contact-btn">Contact Us</div>
</header>

<section class="hero" role="img" aria-label="Modern home exterior lit at dusk">
  <h1>Ferndale – Your Place for “the home”</h1>
  <p>At Ferndale we know “the home, the house” matters: buying a property is one of the most expensive expenses and important assets for people</p>
  <div class="btn">Get Started</div>
</section>

<div class="search-panel">
  <div class="tab buy">
    <div class="ico"><svg width="26" height="26" viewBox="0 0 24 24" fill="none" stroke="#fff" stroke-width="1.8"><path d="M3 11l9-7 9 7M6 9v10h12V9"/></svg></div>
    <div><h3>Buy Properties</h3><small>Lorem ipsum dolor</small></div>
    <div class="chev"><svg width="10" height="10" viewBox="0 0 10 10" fill="none" stroke="#fff" stroke-width="1.8"><path d="M2 3.5l3 3 3-3"/></svg></div>
  </div>
  <div class="tab sell">
    <div class="ico"><svg width="26" height="26" viewBox="0 0 24 24" fill="none" stroke="#fff" stroke-width="1.8"><path d="M4 20V8l6-4v16M10 10h10v10"/></svg></div>
    <div><h3>Sell Properties</h3><small>Lorem ipsum dolor</small></div>
    <div class="chev"><svg width="10" height="10" viewBox="0 0 10 10" fill="none" stroke="#fff" stroke-width="1.8"><path d="M2 6.5l3-3 3 3"/></svg></div>
  </div>
  <div class="filter" style="left:29px"><svg width="12" height="14" viewBox="0 0 12 16" fill="var(--gold)"><path d="M6 0a6 6 0 0 0-6 6c0 4.5 6 10 6 10s6-5.5 6-10a6 6 0 0 0-6-6zm0 8.5A2.5 2.5 0 1 1 6 3.5a2.5 2.5 0 0 1 0 5z"/></svg>Location<span class="dd">⌄</span></div>
  <div class="filter" style="left:219px"><svg width="16" height="14" viewBox="0 0 16 14" fill="none" stroke="var(--gold)" stroke-width="1.5"><rect x="1" y="5" width="14" height="8"/><path d="M4 5V2h8v3"/></svg>Buy<span class="dd">⌄</span></div>
  <div class="filter" style="left:409px"><svg width="14" height="14" viewBox="0 0 14 14" fill="none" stroke="var(--gold)" stroke-width="1.5"><rect x="1" y="1" width="7" height="12"/><rect x="8" y="5" width="5" height="8"/></svg>Office<span class="dd">⌄</span></div>
  <div class="filter" style="left:598px"><svg width="16" height="16" viewBox="0 0 16 16" fill="none" stroke="var(--gold)" stroke-width="1.4"><circle cx="8" cy="8" r="7"/><path d="M10 5.5H7a1.3 1.3 0 0 0 0 2.6h2a1.3 1.3 0 0 1 0 2.6H6M8 4v8"/></svg>Price<span class="dd">⌄</span></div>
  <div class="search-btn">SEARCH</div>
</div>

<section class="about">
  <div class="photo p1" role="img" aria-label="Warm modern living room interior"></div>
  <div class="photo p2" role="img" aria-label="Apartment building exterior under blue sky"></div>
  <div class="logo-box"><i class="sq"></i><span>Ferndale</span></div>
  <h2>ABOUT FERNDALE</h2>
  <h4>At Ferndale, “the home, the house” matters: buying a property is one of the most expensive expenses and important assets for people.</h4>
  <p>Ferndale is a real estate company located in Ferndale Valley, ACT. Being a portfolio sales agent and property manager, coupled with our high-profile international real estate experience, Ferndale is considered a market leader on the cutting edge industry knowledge, ranging from landlord-tenant relationships, residential purchases.</p>
  <div class="contact" style="left:602px"><svg width="14" height="11" viewBox="0 0 14 11" fill="var(--gold)"><path d="M0 0h14v11H0z"/><path d="M0 0l7 6 7-6" stroke="#fff" stroke-width="1.3" fill="none"/></svg>info@ferndaleestatecollective.com.au</div>
  <div class="contact" style="left:902px"><svg width="13" height="13" viewBox="0 0 16 16" fill="var(--gold)"><path d="M3 1l3 3-2 2c1 2 4 5 6 6l2-2 3 3-2 3C7 16 0 9 0 3z"/></svg>02 6100 4321</div>
  <div class="btn">Read More</div>
</section>

<section class="month">
  <div class="section-title" style="top:102px">This Month At <b>Ferndale Estate Collective</b><i class="mark" style="top:52px"></i></div>
  <div class="cat" style="left:111px"><div class="circ" role="img" aria-label="Keys and model house on a contract" style="background:linear-gradient(135deg,#d8d2c8,#b83a2c 55%,#eee)"></div><span>For Sale</span></div>
  <div class="cat active" style="left:320px"><div class="circ" role="img" aria-label="Suburban house with lawn" style="background:linear-gradient(180deg,#9ec3e6,#e7e7e7 55%,#7d9a5a)"></div><span>For Lease</span></div>
  <div class="cat" style="left:528px"><div class="circ" role="img" aria-label="Modern two-storey home at dusk" style="background:linear-gradient(180deg,#3b6fb6,#4a6996 50%,#b48e5a)"></div><span>Open Times</span></div>
  <div class="cat" style="left:737px"><div class="circ" role="img" aria-label="House with a sold sign on the lawn" style="background:linear-gradient(180deg,#f2f2f2,#d9d4c6 50%,#6f9a4e)"></div><span>Sold</span></div>
  <div class="cat" style="left:945px"><div class="circ" role="img" aria-label="Cabin with mountain backdrop" style="background:linear-gradient(180deg,#6e8fbf,#2d3a4c 55%,#a77d4f)"></div><span>Leased</span></div>

  <div class="card" style="left:111px">
    <div class="img" role="img" aria-label="Two-storey home with double garage" style="background:linear-gradient(180deg,#7da3d3,#4e5a63 55%,#a49682)"></div>
    <span class="badge">Sale</span>
    <h3>Hillcrest</h3><div class="price">$1400 pw</div>
    <svg class="eye" width="18" height="12" viewBox="0 0 18 12" fill="none" stroke="#999" stroke-width="1.3"><path d="M1 6s3-5 8-5 8 5 8 5-3 5-8 5-8-5-8-5z"/><circle cx="9" cy="6" r="2.2"/></svg>
    <hr>
    <div class="feat"><div><svg width="22" height="16" viewBox="0 0 22 16" fill="none" stroke="#222" stroke-width="1.5"><path d="M1 15V1M1 10h20v5M3 10V5h16v5"/></svg>4</div><div><svg width="20" height="18" viewBox="0 0 20 18" fill="none" stroke="#222" stroke-width="1.5"><path d="M2 9h16v3a4 4 0 0 1-4 4H6a4 4 0 0 1-4-4zM4 9V3a2 2 0 0 1 4 0"/></svg>2</div><div><svg width="22" height="16" viewBox="0 0 22 16" fill="none" stroke="#222" stroke-width="1.5"><path d="M2 9l2-6h14l2 6v5H2zM2 9h18"/><circle cx="6" cy="12" r="1"/><circle cx="16" cy="12" r="1"/></svg>2</div></div>
    <div class="addr"><svg width="12" height="16" viewBox="0 0 12 16" fill="#222"><path d="M6 0a6 6 0 0 0-6 6c0 4.5 6 10 6 10s6-5.5 6-10a6 6 0 0 0-6-6zm0 8.5A2.5 2.5 0 1 1 6 3.5a2.5 2.5 0 0 1 0 5z"/></svg>9 Banksia Street Hillcrest</div>
    <div class="btn">Click Here</div>
  </div>

  <div class="card" style="left:442px">
    <div class="img" role="img" aria-label="Apartment living room with city view" style="background:linear-gradient(135deg,#cfd3d6,#6b5a4c 55%,#3a3330)"></div>
    <span class="badge red">Un sold</span>
    <h3>Northgate</h3><div class="price">$560 pw</div>
    <svg class="eye" width="18" height="12" viewBox="0 0 18 12" fill="none" stroke="#999" stroke-width="1.3"><path d="M1 6s3-5 8-5 8 5 8 5-3 5-8 5-8-5-8-5z"/><circle cx="9" cy="6" r="2.2"/></svg>
    <hr>
    <div class="feat"><div><svg width="22" height="16" viewBox="0 0 22 16" fill="none" stroke="#222" stroke-width="1.5"><path d="M1 15V1M1 10h20v5M3 10V5h16v5"/></svg>1</div><div><svg width="20" height="18" viewBox="0 0 20 18" fill="none" stroke="#222" stroke-width="1.5"><path d="M2 9h16v3a4 4 0 0 1-4 4H6a4 4 0 0 1-4-4zM4 9V3a2 2 0 0 1 4 0"/></svg>1</div><div><svg width="22" height="16" viewBox="0 0 22 16" fill="none" stroke="#222" stroke-width="1.5"><path d="M2 9l2-6h14l2 6v5H2zM2 9h18"/><circle cx="6" cy="12" r="1"/><circle cx="16" cy="12" r="1"/></svg>1</div></div>
    <div class="addr"><svg width="12" height="16" viewBox="0 0 12 16" fill="#222"><path d="M6 0a6 6 0 0 0-6 6c0 4.5 6 10 6 10s6-5.5 6-10a6 6 0 0 0-6-6zm0 8.5A2.5 2.5 0 1 1 6 3.5a2.5 2.5 0 0 1 0 5z"/></svg>215/2 Kestrel Street Northgate</div>
    <div class="btn">Click Here</div>
  </div>

  <div class="card" style="left:772px">
    <div class="img" role="img" aria-label="Brick bungalow with front garden" style="background:linear-gradient(180deg,#2f6fd0,#a8c4e6 45%,#7b5a45 75%,#6d8d4a)"></div>
    <span class="badge">Sale</span>
    <h3>Eastwood</h3><div class="price">$1300 pw</div>
    <svg class="eye" width="18" height="12" viewBox="0 0 18 12" fill="none" stroke="#999" stroke-width="1.3"><path d="M1 6s3-5 8-5 8 5 8 5-3 5-8 5-8-5-8-5z"/><circle cx="9" cy="6" r="2.2"/></svg>
    <hr>
    <div class="feat"><div><svg width="22" height="16" viewBox="0 0 22 16" fill="none" stroke="#222" stroke-width="1.5"><path d="M1 15V1M1 10h20v5M3 10V5h16v5"/></svg>4</div><div><svg width="20" height="18" viewBox="0 0 20 18" fill="none" stroke="#222" stroke-width="1.5"><path d="M2 9h16v3a4 4 0 0 1-4 4H6a4 4 0 0 1-4-4zM4 9V3a2 2 0 0 1 4 0"/></svg>2</div><div><svg width="22" height="16" viewBox="0 0 22 16" fill="none" stroke="#222" stroke-width="1.5"><path d="M2 9l2-6h14l2 6v5H2zM2 9h18"/><circle cx="6" cy="12" r="1"/><circle cx="16" cy="12" r="1"/></svg>3</div></div>
    <div class="addr"><svg width="12" height="16" viewBox="0 0 12 16" fill="#222"><path d="M6 0a6 6 0 0 0-6 6c0 4.5 6 10 6 10s6-5.5 6-10a6 6 0 0 0-6-6zm0 8.5A2.5 2.5 0 1 1 6 3.5a2.5 2.5 0 0 1 0 5z"/></svg>1 Linden Street Eastwood</div>
    <div class="btn">Click Here</div>
  </div>
</section>

<section class="team">
  <div class="section-title">OUR <em>TEAM</em><i class="mark"></i></div>
  <div class="member" style="left:111px"><div class="strip"><span>LIAM CARTER</span></div><div class="photo" role="img" aria-label="Portrait of team member Liam Carter"></div></div>
  <div class="member" style="left:361px"><div class="strip"><span>NORA QUINN</span></div><div class="photo" role="img" aria-label="Portrait of team member Nora Quinn"></div></div>
  <div class="member" style="left:613px"><div class="strip"><span>ELISE HART</span></div><div class="photo" role="img" aria-label="Portrait of team member Elise Hart"></div></div>
  <div class="member" style="left:862px"><div class="strip"><span>MAYA DUNN</span></div><div class="photo" role="img" aria-label="Portrait of team member Maya Dunn"></div></div>
  <div class="btn">See More</div>
</section>

<section class="testi">
  <div class="section-title">TESTIMONIALS<i class="mark"></i></div>
  <div class="quote" style="left:111px">
    <span class="q1">“</span>
    <p>Liam is my best property manager! Always happy to response my queries and keep us well informed at all stage. I will definitely recommend her to my friends.</p>
    <span class="q2">”</span>
    <h5>OWEN PRATT</h5><small>Lorem ipsum</small>
  </div>
  <div class="quote" style="left:613px">
    <span class="q1">“</span>
    <p>Very good service. Our property manager is very responsible, prompting and cares about detail. They use the system to track everything so no need to worry about miscommunication. I</p>
    <span class="q2">”</span>
    <h5>RUBY LANE</h5><small>Lorem ipsum</small>
  </div>
</section>

<section class="blog">
  <div class="section-title">OUR <em>BLOG</em><i class="mark"></i></div>
  <div class="post" style="left:111px">
    <div class="photo" role="img" aria-label="White modern house with glass frontage" style="background:linear-gradient(180deg,#e9eef3,#d6d6d0 50%,#4c4a45)"></div>
    <div class="date">MAY 19, 2022</div>
    <h3>Lorem ipsum dolor<br>sit amet</h3>
    <p>Lorem ipsum dolor sit amet, consectetur adipiscing elit, sed do eiusmod tempor incididunt ut labore et dolore magna aliqua.</p>
  </div>
  <div class="post" style="left:446px">
    <div class="photo" role="img" aria-label="Hand holding a house-shaped key ring" style="background:linear-gradient(135deg,#f2f0ec,#c7a98a 55%,#5b4636)"></div>
    <div class="date">MAY 19, 2022</div>
    <h3>Lorem ipsum dolor<br>sit amet</h3>
    <p>Lorem ipsum dolor sit amet, consectetur adipiscing elit, sed do eiusmod tempor incididunt ut labore et dolore magna aliqua.</p>
  </div>
  <div class="post" style="left:781px">
    <div class="photo" role="img" aria-label="Apartment towers beside a rooftop pool" style="background:linear-gradient(180deg,#b9cde3,#8a97a6 50%,#3d7bb3)"></div>
    <div class="date">MAY 19, 2022</div>
    <h3>Lorem ipsum dolor<br>sit amet</h3>
    <p>Lorem ipsum dolor sit amet, consectetur adipiscing elit, sed do eiusmod tempor incididunt ut labore et dolore magna aliqua.</p>
  </div>
</section>

<footer class="site-footer">
  <div class="foot-brand"><i class="sq"></i><div><b>Ferndale</b><small>Estate Collective</small></div></div>
  <div class="socials"><i></i><i></i><i></i><i></i></div>
  <div class="fcol" style="left:460px"><h6>Use Link</h6><ul><li style="font-weight:600">Home</li><li>About Us</li><li>Leasing</li><li>Buy</li><li>Sell</li></ul></div>
  <div class="fcol" style="left:644px"><h6>Other Link</h6><ul><li>Termas &amp; condtions</li><li>Privacy Policy</li><li>Support</li><li>Our Team</li><li>Blog</li></ul></div>
  <div class="fcol contact" style="left:894px"><h6>Contact Us</h6><ul>
    <li><svg width="11" height="15" viewBox="0 0 12 16" fill="#fff" style="margin-top:4px;flex:none"><path d="M6 0a6 6 0 0 0-6 6c0 4.5 6 10 6 10s6-5.5 6-10a6 6 0 0 0-6-6zm0 8.5A2.5 2.5 0 1 1 6 3.5a2.5 2.5 0 0 1 0 5z"/></svg>18/4 Wattle Grove Rd,<br>Ferndale, ACT, 2900</li>
    <li><svg width="12" height="12" viewBox="0 0 16 16" fill="#fff" style="margin-top:6px"><path d="M3 1l3 3-2 2c1 2 4 5 6 6l2-2 3 3-2 3C7 16 0 9 0 3z"/></svg>02 6100 4321</li>
    <li><svg width="13" height="10" viewBox="0 0 14 11" fill="#fff" style="margin-top:7px"><path d="M0 0h14v11H0z"/><path d="M0 0l7 6 7-6" stroke="#1b2431" stroke-width="1.3" fill="none"/></svg>info@ferndaleestatecollective.com.au</li>
  </ul></div>
  <div class="copyright">© 2022 ferndaleestatecollective &nbsp;| All Rights Reserved</div>
</footer>

</body>
</html>
```